Redesign for existing homepage

We would like a redesign for our websites 2 column homepage
We provide engine repair and reconditioning services
We would like a cleaner, modern site that works well with our logo colors
Please see the attached brief for more info
Target Market(s)
25 - 45
Industry/Entity Type
Cleaner
Requirements
Must have
- Google Fonts

```html
<!DOCTYPE html>
<html lang="en">
<head>
<meta charset="utf-8">
<title>Marlow Hart Engine Reconditioners</title>
<link href="https://fonts.googleapis.com/css2?family=Open+Sans:wght@400;600&display=swap" rel="stylesheet">
<style>
:root{
  --dark:#1c1c1c;
  --darker:#151515;
  --yellow:#ffc20e;
  --yellow-deep:#ffae00;
  --gold-text:#f5b800;
  --blue:#1a5de0;
  --text:#555;
  --white:#fff;
}
*{box-sizing:border-box;margin:0;padding:0}
html,body{width:1091px;height:1200px;overflow:hidden;background:var(--white)}
body{font-family:"Open Sans",Arial,sans-serif;color:var(--text)}
.page{width:1200px;height:1320px;transform:scale(.90917);transform-origin:0 0;position:relative}
.header{position:absolute;left:0;top:0;width:1200px;height:418px;background:linear-gradient(180deg,#262626,var(--dark));border-top:5px solid var(--yellow)}
.brand{position:absolute;left:100px;top:50px;display:flex;align-items:center;gap:12px}
.brand-dot{width:26px;height:26px;border-radius:50%;background:var(--yellow)}
.brand-name{font-size:28px;font-weight:600;color:var(--yellow)}
.tagline{position:absolute;left:336px;top:37px;color:var(--white);font-size:19px;line-height:30px}
.top-nav{position:absolute;right:102px;top:17px;font-size:13px;color:var(--white)}
.top-nav a{color:var(--white);text-decoration:none}
.phone{position:absolute;right:101px;top:61px;font-size:19px;color:var(--gold-text)}
.hero{position:absolute;left:99px;top:120px;width:1000px;height:250px;background:linear-gradient(110deg,#3a3a3a 0%,#1d1d1d 35%,#4a4a4a 60%,#202020 100%)}
.hero-caption{position:absolute;left:0;top:80px;width:398px;height:84px;background:rgba(45,70,140,.55);padding:11px 27px;color:var(--white);font-size:18px;line-height:30px}
.main-nav{position:absolute;left:99px;top:370px;width:1000px;height:43px;background:linear-gradient(180deg,var(--yellow),var(--yellow-deep));display:flex}
.main-nav a{display:flex;align-items:center;justify-content:center;color:#222;text-decoration:none;font-size:14px;border-right:1px solid #e59a00}
.main-nav a:last-child{border-right:0}
.col{position:absolute;top:443px;width:300px}
.col-photo{width:300px;height:168px;border:1px solid #ccc}
.col h3{margin-top:11px;font-size:16.5px;font-weight:400;color:var(--blue);line-height:24px}
.col p{margin-top:22px;font-size:11.5px;line-height:18px;padding-left:1px}
.btn{display:inline-flex;align-items:center;justify-content:center;margin-top:14px;width:142px;height:38px;border-radius:7px;background:linear-gradient(180deg,var(--yellow),var(--yellow-deep));color:#222;font-size:12px;text-decoration:none;font-family:Arial,sans-serif}
.welcome{position:absolute;left:98px;top:826px;width:660px}
h2{font-size:24px;font-weight:400;color:var(--blue)}
.welcome p{font-size:11.8px;line-height:24px;margin-top:2px}
.features{position:absolute;left:99px;top:1068px;display:flex;gap:10px}
.feature{width:320px;display:flex;gap:12px}
.feature-icon{width:90px;height:100px;border-radius:50%;background:radial-gradient(circle at 40% 40%,#cfcfcf,#555 70%,transparent 72%)}
.feature h4{font-size:18px;font-weight:400;color:var(--blue)}
.feature p{font-size:11.5px;line-height:18px;margin-top:4px}
.feature a{display:block;margin-top:4px;font-size:12px;color:#222;text-decoration:none}
.services{position:absolute;left:799px;top:826px;width:300px}
.services .lead{margin-top:8px;color:var(--gold-text);font-size:14.5px;line-height:24px;padding-left:1px}
.services ul{list-style:none;margin-top:2px;padding-left:1px}
.services li{font-size:12px;line-height:24px}
.services .more{display:block;text-align:right;margin-top:8px;font-size:12px;color:#222;text-decoration:none}
.footer{position:absolute;left:0;top:1218px;width:1200px;height:102px;background:var(--darker);color:var(--white);font-size:12.5px}
.footer-links{position:absolute;left:100px;top:24px}
.footer-links a{color:var(--white);text-decoration:none}
.copyright{position:absolute;left:100px;top:50px}
.badge-square{position:absolute;left:949px;top:23px;width:43px;height:51px;background:var(--yellow)}
.badge-round{position:absolute;left:1007px;top:20px;width:92px;height:56px;border-radius:50%;background:#2a2a2a;border:2px solid #444}
</style>
</head>
<body>
<div class="page">
  <header class="header">
    <div class="brand"><span class="brand-dot"></span><span class="brand-name">Marlow Hart</span></div>
    <p class="tagline">Engine repairs &amp;<br>reconditioning specialists</p>
    <nav class="top-nav"><a href="#">Home</a> / <a href="#">About Us</a> / <a href="#">Contact Us</a></nav>
    <p class="phone">Phone : (04) 555 0192</p>
  </header>
  <section class="hero" role="img" aria-label="Mechanic tightening a bolt in an engine bay">
    <div class="hero-caption">Specialist engine repair &amp; reconditioning<br>To have your car running at its best</div>
  </section>
  <nav class="main-nav">
    <a href="#" style="width:301px">Private Vehicle Service &amp; Repair</a>
    <a href="#" style="width:206px">Trade Customers</a>
    <a href="#" style="width:262px">Race &amp; Classic Car Engines</a>
    <a href="#" style="width:231px">Make an Enquiry</a>
  </nav>

  <article class="col" style="left:99px">
    <div class="col-photo" role="img" aria-label="Two mechanics working under a car bonnet" style="background:linear-gradient(135deg,#6f8fa8,#3b4d66 55%,#2c3646)"></div>
    <h3>Need service and repair for a private vehicle?</h3>
    <p>Get an efficient and honest diagnosis, along with repair work that will have your car running smoothly.</p>
    <a class="btn" href="#">Make an Enquiry</a>
  </article>
  <article class="col" style="left:450px">
    <div class="col-photo" role="img" aria-label="Dealer handing car keys to a customer" style="background:linear-gradient(135deg,#e8ecef,#bfc6cc 50%,#5a5f66)"></div>
    <h3>Interested in becoming a trade customer?</h3>
    <p>You can outsource your the specialist machining jobs to us at very competitive rates.</p>
    <a class="btn" href="#">Trade Customer</a>
  </article>
  <article class="col" style="left:800px">
    <div class="col-photo" role="img" aria-label="Race car cornering on a track" style="background:linear-gradient(160deg,#6b7a5a,#9aa080 45%,#c9c2b0 60%,#6d6a58)"></div>
    <h3>Is your classic or race car your passion?</h3>
    <p>s your vintage car just sitting in your garage? Contact us to get the engine on your classic car or race</p>
    <a class="btn" href="#" style="margin-left:2px">Contact Us</a>
  </article>

  <section class="welcome">
    <h2>Welcome Our Website !</h2>
    <p>Lorem Ipsum is simply dummy text of the printing and typesetting industry. Lorem Ipsum has been the industry's standard dummy text ever since the 1500s, when an unknown printer took a galley of type and scrambled it to make a type specimen book. It has survived not only five centuries, but also the leap into electronic typesetting, remaining essentially unchanged. It Lorem Ipsum is simply dummy text of the printing and typesetting industry. Lorem Ipsum has been the industry's standard dummy text ever since the 1500s, when an unknown printer took a galley of type and scrambled it to make a type specimen book. It has survived not only five centuries, but also the leap into electronic typesetting, remaining essentially unchanged. It Lorem Ipsum is simply dummy text of the printing and typesetting industry.</p>
  </section>
  <div class="features">
    <div class="feature">
      <div class="feature-icon" role="img" aria-label="Engine gear and piston icon"></div>
      <div><h4>Engine Repair</h4><p>Lorem ipsum dolosit amet, consetetur sadipng elitr sed diam nonumy eirmod.</p><a href="#">Read More +</a></div>
    </div>
    <div class="feature">
      <div class="feature-icon" role="img" aria-label="Car wheel and tyre icon"></div>
      <div><h4>Wheel Alignment</h4><p>Lorem ipsum dolosit amet, consetetur sadipng elitr sed diam nonumy eirmod.</p><a href="#">Read More +</a></div>
    </div>
  </div>

  <aside class="services">
    <h2>Our Services</h2>
    <p class="lead">Dolor sit amet, consectetur adipisicing elit, sed do eiusmo.</p>
    <ul>
      <li>Complete Computer Diagnostics</li>
      <li>Complete Safety Analysis</li>
      <li>Drivability Problems</li>
      <li>Tune-ups</li>
      <li>Oil Changes</li>
      <li>Tires</li>
      <li>Brake repair specialists</li>
      <li>Mufflers and Exhaust Systems</li>
      <li>Steering and Suspensions</li>
    </ul>
    <a class="more" href="#">- Read More +</a>
  </aside>

  <footer class="footer">
    <nav class="footer-links"><a href="#">Home</a> | <a href="#">About</a> | <a href="#">Practices</a> | <a href="#">People</a> | <a href="#">Events</a> | <a href="#">Contact</a> | <a href="#">Site Map</a> | <a href="#">Privacy Policy</a></nav>
    <p class="copyright">Copyright © 2014 Marlow Hart. All Rights Reserved</p>
    <div class="badge-square"></div>
    <div class="badge-round"></div>
  </footer>
</div>
</body>
</html>
```